Equipment Finance Specialist I work with companies who need the funds to buy their equipment

I would like a business card that stands out on the shelves. I want to be able to hand it to someone and say WOW. This card should have my logo.
You can put color into it I am very open on design and color

What my company does is we deal with dealerships that sell equipment such as Dump Trucks garbage trucks tractors trailers. Customers get referred to us and depending on their time in business we will ask for the following items

Companies that have been in business for more than two years we have a credit application program up to 250K . With this program we need the following items Credit application filled out(which is what I would like to be able for the customer to click on my website to get.) as well as three current month bank statements.

Deals over 250k we will need the following items

2 years business tax returns
2 years personal tax returns
Profit & Loss statement
Personal Financial Statement

what we do
100% FINANCING
SEASONAL PAYMENTS
LOAN BALLOON PAYMENTS
TRAC LEASING
LOW-INTEREST REFINANCING RATES
DEBT CONSOLIDATION

We specialize in creative financing solutions and offer a variety of reliable, flexible and expandable lending choices.

Target Market(s)

Trucking Companies

Industry/Entity Type

Trucking Company

Contact Information for Business Card

* $250,000 Application only Program
* Loans from $30,000 to 5,000,000
* Competitive Interest Rates

Font styles to use
Serif
Sans Serif

Colors

Designer to choose colors to be used in the design.

Requirements
Must have
• On the back of the card.
• * $250,000 Application only Program
• * Loans from $30,000 to 5,000,000
• My name, email, website. address
• * Competitive Interest Rates
• * 100% Financing
Nice to have
• I want my logo to pop on the card
• My logo is the great one I would like to use
Should not have
• I am up for your creativity as well

```html
<!DOCTYPE html>
<html lang="en">
<head>
<meta charset="utf-8">
<title>Summit Lending – Business Card</title>
<link href="https://fonts.googleapis.com/css2?family=Open+Sans:wght@400;600;700;800&display=swap" rel="stylesheet">
<style>
  :root {
    --navy: #0f2f7a;
    --navy-deep: #0a2462;
    --navy-light: #1a3f96;
    --red: #c8102e;
    --white: #ffffff;
    --ink: #3a3a3a;
    --stage: #e9ebef;
  }
  * { box-sizing: border-box; margin: 0; padding: 0; }
  html, body { width: 1200px; height: 892px; overflow: hidden; }
  body {
    background: var(--stage);
    font-family: "Open Sans", Arial, sans-serif;
    position: relative;
  }
  .card {
    position: absolute;
    width: 620px;
    height: 354px;
    box-shadow: 0 10px 30px rgba(0,0,0,.25);
    overflow: hidden;
  }
  /* Back side */
  .card-back {
    left: 40px; top: 60px;
    background: linear-gradient(150deg, var(--navy-light) 0%, var(--navy) 50%, var(--navy-deep) 100%);
    color: var(--white);
  }
  .back-brand {
    position: absolute;
    left: 60px; top: 110px;
    display: flex; align-items: center; gap: 16px;
  }
  .brand-circle {
    width: 110px; height: 110px;
    border-radius: 50%;
    border: 8px solid var(--white);
    flex: none;
  }
  .back-brand .brand-name {
    font-weight: 800; font-size: 20px; letter-spacing: .5px; line-height: 1.15;
  }
  .feature-list {
    position: absolute;
    left: 330px; top: 118px;
    list-style: none;
    font-size: 15px; font-weight: 600; line-height: 1.45;
  }
  .feature-list li::before {
    content: ""; display: inline-block;
    width: 6px; height: 6px; border-radius: 50%;
    background: var(--white); margin-right: 8px; vertical-align: middle;
  }
  /* Front side */
  .card-front {
    left: 540px; top: 478px;
    background: var(--white);
  }
  .front-brand {
    position: absolute;
    left: 170px; top: 86px;
    display: flex; align-items: center; gap: 12px;
  }
  .front-brand .brand-dot {
    width: 62px; height: 62px; border-radius: 50%;
    background: var(--navy); flex: none;
  }
  .front-brand .brand-name {
    font-weight: 800; font-size: 34px; color: var(--navy); letter-spacing: 1px;
  }
  .contact {
    position: absolute;
    right: 36px; top: 150px;
    font-size: 14px; color: var(--ink); line-height: 1.4;
  }
  .contact .address { margin-bottom: 8px; }
  .contact-row { display: flex; align-items: center; gap: 9px; }
  .contact-row svg { width: 14px; height: 14px; fill: var(--navy); flex: none; }
  .person {
    position: absolute; left: 40px; bottom: 74px;
  }
  .person .name {
    font-weight: 800; font-size: 22px; color: var(--navy); letter-spacing: .5px;
  }
  .person .title {
    font-size: 16px; color: var(--red); letter-spacing: .5px; margin-top: -2px;
  }
  .front-band {
    position: absolute; left: 0; right: 0; bottom: 0;
    height: 34px; background: var(--navy);
  }
</style>
</head>
<body>

<section class="card card-back" aria-label="Card back">
  <div class="back-brand">
    <div class="brand-circle"></div>
    <div class="brand-name">SUMMIT<br>LENDING</div>
  </div>
  <ul class="feature-list">
    <li>$250,000 Application only Program</li>
    <li>Loans from $30,000 to 5,000,000</li>
    <li>Competitive Interest Rates</li>
    <li>100% Financing</li>
  </ul>
</section>

<section class="card card-front" aria-label="Card front">
  <div class="front-brand">
    <div class="brand-dot"></div>
    <div class="brand-name">SUMMIT LENDING</div>
  </div>

  <div class="contact">
    <div class="address">412 Harbor Lane<br>Glen Cove, NY 11542</div>
    <div class="contact-row">
      <svg viewBox="0 0 24 24"><path d="M6.6 10.8a15.1 15.1 0 0 0 6.6 6.6l2.2-2.2c.3-.3.7-.4 1-.2 1.1.4 2.3.6 3.6.6.6 0 1 .4 1 1V20c0 .6-.4 1-1 1A17 17 0 0 1 3 4c0-.6.4-1 1-1h3.5c.6 0 1 .4 1 1 0 1.3.2 2.5.6 3.6.1.3 0 .7-.2 1z"/></svg>
      <span>555 0142 7788</span>
    </div>
    <div class="contact-row">
      <svg viewBox="0 0 24 24"><path d="M2 5h20v14H2z" fill="none"/><path d="M2 5h20v14H2V5zm2 2v.5l8 5 8-5V7H4z"/></svg>
      <span>mark@summitlending.com</span>
    </div>
    <div class="contact-row">
      <svg viewBox="0 0 24 24"><circle cx="12" cy="12" r="10"/></svg>
      <span>www.summitlending.com</span>
    </div>
  </div>

  <div class="person">
    <div class="name">MARK ROWAN</div>
    <div class="title">PRESIDENT</div>
  </div>

  <div class="front-band"></div>
</section>

</body>
</html>
```